Crestline Build Advisors Trade Show

We need the design for tree retractable banners for a trade show. Each banner is 33.5"x 78.7" I'm attaching a sample of a possible lay out. Also you can check on our web site (currently under construction) about the language we use on it. We want something similar in the three (3) banners. The following is the link: http://cba2.pelvaronsites.net/#services. In addition, I have attached the logos of some of our clients that we would like to incorporate in the banners.
Please do not hesitate to contact me with any questions

Target Market(s)

Architects, Developers, Real Estate Companies, Construction Companies

Requirements
Must have
• Clients and Services... See web site for referencing
• http://cba2.pelvaronsites.net

```html
<!DOCTYPE html>
<html lang="en">
<head>
<meta charset="utf-8">
<title>Crestline Build Advisors – Retractable Banner</title>
<link rel="stylesheet" href="https://fonts.googleapis.com/css2?family=Montserrat:ital,wght@0,400;0,700;1,600;1,700&display=swap">
<style>
  :root {
    --page-bg: #eceded;
    --sky-top: #e4f0fa;
    --sky-bottom: #f6f9fc;
    --brand-blue: #1f74c4;
    --band-blue: #2b98d8;
    --rule-black: #111111;
    --body-ink: #1c1c1c;
    --white: #ffffff;
    --emblem-green: #5a9e32;
    --emblem-orange: #f0a52a;
    --emblem-blue: #2a86d2;
  }
  * { box-sizing: border-box; margin: 0; padding: 0; }
  html, body {
    width: 1200px;
    height: 1000px;
    overflow: hidden;
    background: var(--page-bg);
    font-family: "Montserrat", Arial, sans-serif;
  }
  .banner {
    position: absolute;
    left: 405px;
    top: 45px;
    width: 390px;
    height: 910px;
    overflow: hidden;
    background: linear-gradient(180deg, var(--sky-top) 0%, var(--sky-bottom) 55%, var(--sky-top) 90%);
    box-shadow: 0 2px 8px rgba(0,0,0,0.18);
  }
  .emblem-art {
    position: absolute;
    left: 40px;
    top: 0;
    width: 350px;
    height: 500px;
    border-bottom-left-radius: 160px;
    background:
      radial-gradient(circle at 85% 18%, var(--emblem-orange) 0%, rgba(240,165,42,0.6) 28%, rgba(240,165,42,0) 48%),
      radial-gradient(circle at 80% 78%, var(--emblem-blue) 0%, rgba(42,134,210,0.6) 28%, rgba(42,134,210,0) 50%),
      radial-gradient(circle at 30% 50%, var(--emblem-green) 0%, rgba(90,158,50,0.55) 32%, rgba(90,158,50,0) 58%),
      #d9e8f2;
  }
  .pitch {
    position: absolute;
    left: 0;
    top: 574px;
    width: 100%;
    text-align: center;
    font-style: italic;
    font-weight: 600;
    font-size: 19px;
    line-height: 26.3px;
    color: var(--body-ink);
  }
  .pitch .company-name {
    font-weight: 700;
    color: var(--brand-blue);
  }
  .footer-rule {
    position: absolute;
    left: 0;
    top: 831px;
    width: 100%;
    height: 6px;
    background: var(--rule-black);
  }
  .footer-band {
    position: absolute;
    left: 0;
    top: 837px;
    width: 100%;
    height: 73px;
    background: var(--band-blue);
    display: flex;
    align-items: center;
    justify-content: center;
    color: var(--white);
    font-size: 19px;
    font-weight: 400;
    letter-spacing: 0.2px;
  }
  .footer-band strong { font-weight: 700; }
</style>
</head>
<body>
  <main class="banner">
    <div class="emblem-art" role="img" aria-label="Emblem illustration of a green leaf, orange sun and blue water drop"></div>

    <p class="pitch">
      <span class="company-name">Crestline Build Advisors</span><br>
      understands how to balance<br>
      the scope, budget, time, and<br>
      requirements to ensure<br>
      completed programs and<br>
      projects meet or surpass the<br>
      owner/client’s expectations<br>
      and triple bottom line goals.
    </p>

    <div class="footer-rule"></div>
    <div class="footer-band">www.<strong>websitename</strong>.com</div>
  </main>
</body>
</html>
```